Brewlark Cup Society - A Monthly Subscription Coffee Club - Shopify Website Design

A monthly subscription company. Need a Shopify Website Design and uploaded to fully work with Tidal Renewals.

Please look at these sites for examples as well as the images I enclosed.

https://www.sipvantor.com/
https://mokrate.com/
https://www.platewinder.com/
https://www.globunchies.com/

Number of Pages Required

1 page

```html
<!DOCTYPE html>
<html lang="en">
<head>
<meta charset="utf-8">
<title>Brewlark Cup Society — Coffee Subscription</title>
<link rel="stylesheet" href="https://fonts.googleapis.com/css2?family=Cormorant+Garamond:wght@500;600;700&family=Open+Sans:wght@400;600&display=swap">
<style>
:root{
  --ink:#1c1c1c;
  --text:#444;
  --muted:#8a8a8a;
  --line:#d9d9d9;
  --bar:#2b2b2b;
  --hero:#ececec;
  --band:#e8e8e8;
  --white:#fff;
  --coffee:#4a2a17;
  --kraft:#d9a07f;
}
*{box-sizing:border-box;margin:0;padding:0}
html,body{width:1200px;height:2932px;overflow:hidden;background:var(--white)}
body{position:relative;font-family:"Open Sans",Arial,sans-serif;color:var(--text)}
.abs{position:absolute}

.announce{left:0;top:0;width:1200px;height:24px;background:var(--bar);color:#ddd;font-size:10px;display:flex;align-items:center;justify-content:center}

.site-header{left:0;top:24px;width:1200px;height:80px;display:flex;align-items:center;justify-content:space-between;padding:0 112px}
.brand{font-family:"Cormorant Garamond",Georgia,serif;font-weight:700;font-size:22px;letter-spacing:1px;color:var(--ink)}
.header-tools{display:flex;align-items:center;gap:18px}
.join-btn{border:1.5px solid var(--ink);font-size:12px;padding:4px 12px;color:var(--ink)}

.hero{left:0;top:104px;width:1200px;height:456px;background:var(--hero)}
.hero-product{left:520px;top:50px;width:540px;height:406px;background:radial-gradient(ellipse 60% 55% at 60% 55%,rgba(200,140,105,.75),rgba(110,62,35,.55) 55%,rgba(236,236,236,0) 100%)}
.hero-title{left:112px;top:96px;z-index:2;white-space:nowrap;font-family:"Cormorant Garamond",Georgia,serif;font-weight:600;font-size:52px;line-height:50px;color:var(--ink);letter-spacing:1px}

.tabs{left:112px;top:620px;display:flex}
.tab{font-family:"Cormorant Garamond",Georgia,serif;font-weight:700;font-size:22px;color:var(--ink);width:212px;padding-bottom:10px;white-space:nowrap}
.tab sup{font-size:10px}
.tab.active{border-bottom:3px solid var(--ink)}
.tabs-rule{left:112px;top:672px;width:976px;height:1px;background:var(--line)}

.card{width:468px;height:190px;padding:18px 16px;border-bottom:1px solid var(--line)}
.card.raised{background:var(--white);box-shadow:0 4px 20px rgba(0,0,0,.18);border-bottom:none}
.card-title{font-family:"Cormorant Garamond",Georgia,serif;font-weight:700;font-size:18px;color:var(--ink)}
.card-price{font-size:13px;color:var(--ink);margin-top:4px}
.card-desc{font-size:12px;line-height:18px;width:300px;margin-top:18px;color:var(--text)}
.card-photo{position:absolute;right:16px;top:18px;width:112px;height:96px}

.gift{left:0;top:1420px;width:1200px;height:520px;background:var(--band)}
.gift-photo{left:180px;top:80px;width:360px;height:320px;background:radial-gradient(ellipse 65% 60% at 45% 50%,#dca07c,#c98a64 55%,rgba(232,232,232,0) 100%)}
.gift-title{left:620px;top:104px;font-family:"Cormorant Garamond",Georgia,serif;font-weight:500;font-size:42px;color:var(--ink);letter-spacing:1px}
.gift-price{left:620px;top:166px;font-size:13px;color:var(--ink)}
.add-btn{left:620px;top:204px;width:320px;height:40px;border:1.5px solid var(--ink);font-size:12px;font-weight:600;color:var(--ink);display:flex;align-items:center;justify-content:center;letter-spacing:.5px}
.gift-desc{left:620px;top:276px;width:360px;font-size:13px;line-height:20px}

.about-title{left:120px;top:2150px;font-family:"Cormorant Garamond",Georgia,serif;font-weight:500;font-size:42px;color:var(--ink);letter-spacing:1px}
.about-desc{left:120px;top:2210px;width:420px;font-size:13px;line-height:20px}
.about-photo{left:600px;top:2040px;width:488px;height:460px;background:radial-gradient(circle at 22% 20%,#efe9e2 0 16%,transparent 30%),linear-gradient(140deg,#6b4428,#3a2213 60%,#24140a)}

.footer-rule{left:0;top:2590px;width:1200px;height:1px;background:var(--line)}
.foot-head{font-family:"Cormorant Garamond",Georgia,serif;font-weight:700;font-size:24px;color:var(--ink);letter-spacing:1px}
.foot-text{font-size:13px;line-height:20px;color:var(--text)}
.email-field{left:600px;top:2724px;width:320px;height:34px;border-bottom:1px solid var(--ink);font-size:11px;color:var(--muted);padding-top:14px}
.subscribe-btn{left:944px;top:2720px;width:136px;height:42px;border:1.5px solid var(--ink);font-size:12px;font-weight:600;color:var(--ink);display:flex;align-items:center;justify-content:center}
.copyright{left:112px;top:2846px;font-size:12px;color:var(--ink)}
.copyright span{margin:0 24px}
</style>
</head>
<body>

<div class="abs announce">Join today and get free shipping on your very first monthly coffee box delivery.</div>

<header class="abs site-header">
  <div class="brand">BREWLARK CUP SOCIETY</div>
  <div class="header-tools">
    <svg width="18" height="18" viewBox="0 0 18 18" aria-label="Search"><circle cx="7.5" cy="7.5" r="5.5" fill="none" stroke="#1c1c1c" stroke-width="2"/><line x1="11.5" y1="11.5" x2="16" y2="16" stroke="#1c1c1c" stroke-width="2"/></svg>
    <svg width="20" height="18" viewBox="0 0 20 18" aria-label="Cart"><path d="M1 2h3l2.5 10h10L19 5H5.5" fill="none" stroke="#1c1c1c" stroke-width="2"/><circle cx="8" cy="15.5" r="1.5" fill="#1c1c1c"/><circle cx="15" cy="15.5" r="1.5" fill="#1c1c1c"/></svg>
    <div class="join-btn">Join</div>
  </div>
</header>

<section class="abs hero">
  <div class="abs hero-product" role="img" aria-label="Kraft coffee subscription box with roasted coffee beans spilling in front"></div>
  <h1 class="abs hero-title">THE BEST COFFEE<br>SUBSCRIPTION<br>BOX</h1>
</section>

<nav class="abs tabs">
  <div class="tab active">LOREM IPSUM <sup>(4)</sup></div>
  <div class="tab">LOREM IPSUM <sup>(2)</sup></div>
  <div class="tab">LOREM IPSUM <sup>(3)</sup></div>
  <div class="tab">LOREM IPSUM <sup>(6)</sup></div>
</nav>
<div class="abs tabs-rule"></div>

<section class="products">
  <article class="abs card raised" style="left:112px;top:700px">
    <div class="card-title">LOREM IPSUM DOLOR</div><div class="card-price">$ 20.00</div>
    <p class="card-desc">Lorem ipsum dolor sit amet, consectetur adipiscing elit, sed do eiusmod tempor incididunt dolore magna aliqua. Ut enim ad minim veniam, quis.</p>
    <div class="card-photo" role="img" aria-label="Coffee beans on a dark tray" style="background:linear-gradient(135deg,#6b3f24,#2a170b)"></div>
  </article>
  <article class="abs card" style="left:620px;top:700px">
    <div class="card-title">LOREM IPSUM DOLOR</div><div class="card-price">$ 20.00</div>
    <p class="card-desc">Lorem ipsum dolor sit amet, consectetur adipiscing elit, sed do eiusmod tempor incididunt dolore magna aliqua. Ut enim ad minim veniam, quis.</p>
    <div class="card-photo" role="img" aria-label="Close-up of roasted coffee beans" style="background:linear-gradient(135deg,#7a3a26,#3a1a10)"></div>
  </article>
  <article class="abs card" style="left:112px;top:920px">
    <div class="card-title">LOREM IPSUM DOLOR</div><div class="card-price">$ 20.00</div>
    <p class="card-desc">Lorem ipsum dolor sit amet, consectetur adipiscing elit, sed do eiusmod tempor incididunt dolore magna aliqua. Ut enim ad minim veniam, quis.</p>
    <div class="card-photo" role="img" aria-label="Wooden box with compartments of coffee" style="background:linear-gradient(135deg,#5a2c1c,#2b120a)"></div>
  </article>
  <article class="abs card" style="left:620px;top:920px">
    <div class="card-title">LOREM IPSUM DOLOR</div><div class="card-price">$ 20.00</div>
    <p class="card-desc">Lorem ipsum dolor sit amet, consectetur adipiscing elit, sed do eiusmod tempor incididunt dolore magna aliqua. Ut enim ad minim veniam, quis.</p>
    <div class="card-photo" role="img" aria-label="Cup of coffee surrounded by beans" style="background:linear-gradient(135deg,#8a5a3a,#2e1a0e)"></div>
  </article>
  <article class="abs card" style="left:112px;top:1140px">
    <div class="card-title">LOREM IPSUM DOLOR</div><div class="card-price">$ 20.00</div>
    <p class="card-desc">Lorem ipsum dolor sit amet, consectetur adipiscing elit, sed do eiusmod tempor incididunt dolore magna aliqua. Ut enim ad minim veniam, quis.</p>
    <div class="card-photo" role="img" aria-label="Coffee beans on an orange background" style="background:linear-gradient(135deg,#f06a2a,#c3471a)"></div>
  </article>
  <article class="abs card" style="left:620px;top:1140px">
    <div class="card-title">LOREM IPSUM DOLOR</div><div class="card-price">$ 20.00</div>
    <p class="card-desc">Lorem ipsum dolor sit amet, consectetur adipiscing elit, sed do eiusmod tempor incididunt dolore magna aliqua. Ut enim ad minim veniam, quis.</p>
    <div class="card-photo" role="img" aria-label="Coffee being brewed on a wooden table" style="background:linear-gradient(135deg,#9a7a5a,#3a2516)"></div>
  </article>
</section>

<section class="abs gift">
  <div class="abs gift-photo" role="img" aria-label="Open kraft gift box holding three coffee pouches beside scattered beans"></div>
  <h2 class="abs gift-title">GIFT BOXES</h2>
  <div class="abs gift-price">$ 100.00</div>
  <div class="abs add-btn">ADD TO CART</div>
  <p class="abs gift-desc">Lorem ipsum dolor sit amet, consectetur adipiscing elit, sed do eiusmod tempor incididunt ut labore et dolore magna aliqua. Ut enim ad minim veniam, quis nostrud exercitation ullamco laboris nisi ut aliquip ex ea commodo consequat.</p>
</section>

<section class="about">
  <h2 class="abs about-title">ABOUT US</h2>
  <p class="abs about-desc">Lorem ipsum dolor sit amet, consectetur adipiscing elit, sed do eiusmod tempor incididunt ut labore et dolore magna aliqua. Ut enim ad minim veniam, quis nostrud exercitation ullamco laboris nisi ut aliquip ex ea commodo consequat.</p>
  <div class="abs about-photo" role="img" aria-label="Espresso cup beside a wooden crate of coffee beans and cinnamon sticks"></div>
</section>

<footer>
  <div class="abs footer-rule"></div>
  <div class="abs foot-head" style="left:112px;top:2652px">CONTACT</div>
  <p class="abs foot-text" style="left:112px;top:2710px">123 Lorem ipsum dolor sit amet,<br>consectetur adipiscing</p>
  <p class="abs foot-text" style="left:112px;top:2782px">(555) 014-2287</p>
  <div class="abs foot-head" style="left:600px;top:2652px">NEWSLETTER</div>
  <div class="abs email-field">Email Address</div>
  <div class="abs subscribe-btn">SUBSCRIBE</div>
  <div class="abs copyright">[ C ] Copyrights 2020 Brewlark Cup Society<span>|</span>All Rights Reserved</div>
</footer>

</body>
</html>
```